Solar WiFi Charging Bench

Sales Brochure using only the colors of the Copperwren Color Palette provided.
Municipal Government target customer.
Key Features are as follows:
LED Advertising display
Connection to internet (User Defined)
800W Solar
USB-A and USB-C cell phone charging ports
400ah battery backup with low voltage shutoff
Insulated for -40 Deg C
Wireless cell phone charging
Vandalism resistant.
Theft resistant

```html
<!DOCTYPE html>
<html lang="en">
<head>
<meta charset="utf-8">
<title>Solar WiFi Charging Bench – Key Features</title>
<link rel="stylesheet" href="https://fonts.googleapis.com/css2?family=Montserrat:wght@600;700;800;900&family=Oswald:wght@500&display=swap">
<style>
  :root {
    --navy: #3f56a8;
    --sky: #44c7ef;
    --leaf: #6cbb45;
    --ink: #4a4a4a;
    --icon-fill: #cdeffb;
    --icon-stroke: #2f49a3;
    --paper: #ffffff;
    --bench-top: #d9d6d0;
    --bench-mid: #b9b3a9;
    --bench-low: #8e7a62;
  }
  * { margin: 0; padding: 0; box-sizing: border-box; }
  html, body { width: 787px; height: 1200px; overflow: hidden; background: var(--paper); }
  .sheet { position: relative; width: 787px; height: 1200px; background: var(--paper); font-family: "Montserrat", sans-serif; overflow: hidden; }

  .header-band { position: absolute; inset: 0; width: 787px; height: 260px; }

  .brand { position: absolute; left: 40px; top: 118px; display: flex; align-items: center; gap: 8px; }
  .brand-dot { width: 14px; height: 14px; border-radius: 50%; background: var(--sky); }
  .brand-name { font-weight: 800; font-size: 21px; color: var(--navy); line-height: 1.15; }

  .title { position: absolute; left: 280px; top: 42px; color: var(--paper); font-weight: 900; line-height: 1; letter-spacing: 0.5px; }
  .title-line { display: block; font-size: 49px; }
  .title-line.second { font-size: 40px; margin-top: 6px; }
  .title-accent { color: var(--sky); }

  .key-features { position: absolute; left: 302px; top: 192px; width: 416px; text-align: center; font-weight: 900; font-size: 34px; color: var(--paper); letter-spacing: 0.5px; }

  .bench-photo { position: absolute; left: 222px; top: 318px; width: 355px; height: 535px;
    background: linear-gradient(170deg, var(--bench-top) 0%, #ece9e4 45%, var(--bench-mid) 72%, var(--bench-low) 86%, #e7e7e7 100%);
    clip-path: polygon(28% 0, 100% 22%, 72% 34%, 68% 92%, 30% 100%, 0 93%, 0 40%, 14% 18%); }

  .diagram { position: absolute; inset: 0; width: 787px; height: 1200px; }

  .feature-label { position: absolute; width: 170px; margin-left: -85px; text-align: center; font-weight: 700; font-size: 13.5px; line-height: 15px; color: var(--ink); }

  .footer { position: absolute; left: 0; top: 1090px; width: 787px; height: 110px; background: var(--sky); color: var(--paper); }
  .footer-cta { position: absolute; left: 44px; top: 16px; font-weight: 800; font-size: 15px; color: var(--navy); letter-spacing: 0.3px; }
  .footer-phone { position: absolute; top: 44px; font-family: "Oswald", sans-serif; font-weight: 500; font-size: 27px; display: flex; align-items: center; gap: 4px; }
  .footer-phone svg { width: 17px; height: 17px; }
  .footer-divider { position: absolute; top: 50px; height: 42px; border-left: 1.5px dashed var(--paper); }
  .footer-info { position: absolute; top: 51px; font-weight: 600; font-size: 12px; line-height: 16px; display: flex; gap: 6px; }
  .footer-info svg { width: 11px; height: 11px; margin-top: 2px; flex: none; }
  .footer-contacts { position: absolute; left: 525px; top: 50px; font-weight: 600; font-size: 12px; line-height: 17px; }
  .footer-contacts div { display: flex; align-items: center; gap: 6px; }
  .footer-contacts svg { width: 11px; height: 11px; }
</style>
</head>
<body>
<main class="sheet">

  <svg class="header-band" viewBox="0 0 787 260" aria-hidden="true">
    <polygon points="205,0 787,0 787,208 250,208" fill="var(--navy)"/>
    <polygon points="300,189 727,189 718,250 293,250" fill="var(--leaf)"/>
    <g fill="none" stroke="var(--paper)" stroke-width="5">
      <path d="M757,0 A30,30 0 0 0 787,30"/>
      <path d="M742,0 A45,45 0 0 0 787,45"/>
      <path d="M727,0 A60,60 0 0 0 787,60"/>
    </g>
  </svg>

  <div class="brand">
    <span class="brand-dot"></span>
    <span class="brand-name">Copperwren<br>Renewables</span>
  </div>

  <h1 class="title">
    <span class="title-line">SOLAR <span class="title-accent">WIFI</span></span>
    <span class="title-line second">CHARGING BENCH</span>
  </h1>
  <div class="key-features">KEY FEATURES</div>

  <div class="bench-photo" role="img" aria-label="Photo of the solar WiFi charging bench with curved solar canopy, wooden seat and white panelled base"></div>

  <svg class="diagram" viewBox="0 0 787 1200" aria-hidden="true">
    <g fill="none" stroke="var(--leaf)" stroke-width="3">
      <polyline points="131,298 131,268 224,268 224,429 280,429"/>
      <polyline points="163,507 204,507 204,555 224,555"/>
      <polyline points="163,715 215,715"/>
      <polyline points="260,968 276,968 276,887"/>
      <polyline points="359,887 359,851 388,851 388,815"/>
      <polyline points="452,812 486,851 486,942 597,942"/>
      <polyline points="475,754 492,777 591,777"/>
      <polyline points="499,585 591,585"/>
      <polyline points="530,364 602,292 649,292"/>
    </g>
    <g fill="var(--paper)" stroke="var(--leaf)" stroke-width="2.5">
      <circle cx="131" cy="298" r="4.5"/><circle cx="280" cy="429" r="4.5"/>
      <circle cx="163" cy="507" r="4.5"/><circle cx="224" cy="555" r="4.5"/>
      <circle cx="163" cy="715" r="4.5"/><circle cx="215" cy="715" r="4.5"/>
      <circle cx="260" cy="968" r="4.5"/><circle cx="276" cy="887" r="4.5"/>
      <circle cx="359" cy="887" r="4.5"/><circle cx="388" cy="815" r="4.5"/>
      <circle cx="452" cy="812" r="4.5"/><circle cx="597" cy="942" r="4.5"/>
      <circle cx="475" cy="754" r="4.5"/><circle cx="591" cy="777" r="4.5"/>
      <circle cx="499" cy="585" r="4.5"/><circle cx="591" cy="585" r="4.5"/>
      <circle cx="530" cy="364" r="4.5"/><circle cx="649" cy="292" r="4.5"/>
    </g>

    <g fill="var(--icon-fill)" stroke="var(--sky)" stroke-width="2.5">
      <circle cx="138" cy="395" r="40"/>
      <circle cx="138" cy="583" r="40"/>
      <circle cx="138" cy="787" r="40"/>
      <circle cx="138" cy="968" r="40"/>
      <circle cx="392" cy="968" r="40"/>
      <circle cx="649" cy="395" r="40"/>
      <circle cx="649" cy="583" r="40"/>
      <circle cx="649" cy="775" r="40"/>
      <circle cx="649" cy="968" r="40"/>
    </g>

    <g fill="none" stroke="var(--icon-stroke)" stroke-width="2.2" stroke-linecap="round" stroke-linejoin="round">
      <!-- LED display -->
      <rect x="120" y="381" width="36" height="24" rx="2"/>
      <path d="M132,405 L130,413 M144,405 L146,413 M126,413 H150"/>
      <!-- internet cloud + phone -->
      <path d="M119,594 a9,9 0 0 1 3,-17 a12,12 0 0 1 23,-3 a9,9 0 0 1 5,20 Z"/>
      <rect x="132" y="578" width="12" height="19" rx="2"/>
      <!-- solar panel -->
      <path d="M122,774 H154 L150,796 H126 Z M124,781 H152 M123,788 H151 M133,774 L132,796 M143,774 L144,796 M138,796 V805 M130,805 H146"/>
      <!-- USB plug -->
      <path d="M129,955 H147 V976 L142,982 H134 L129,976 Z M134,982 V990 M142,982 V990 M138,960 L135,968 H141 L138,975"/>
      <!-- battery -->
      <rect x="373" y="955" width="32" height="26" rx="2"/>
      <path d="M373,962 H405 M379,958 H385 M381,967 L378,974 H384 L381,980"/>
      <rect x="390" y="968" width="11" height="14" rx="1"/>
      <!-- wireless pad -->
      <path d="M631,400 V410 H667 V400 M640,400 V404 H658 V400 M641,388 a11,11 0 0 1 16,0 M645,392 a5,5 0 0 1 8,0 M649,394 L647,400 H651 L649,405"/>
      <!-- building -->
      <path d="M642,603 V567 L652,562 L660,567 V603 Z M630,603 H668 M646,573 H656 M646,581 H656 M646,589 H656 M634,603 V592 L640,588"/>
      <!-- safe -->
      <rect x="631" y="757" width="36" height="36" rx="2"/>
      <rect x="636" y="762" width="26" height="26"/>
      <circle cx="649" cy="775" r="6"/><circle cx="649" cy="775" r="2"/>
      <!-- thermometer -->
      <path d="M645,950 a4,4 0 0 1 8,0 V972 a7,7 0 1 1 -8,0 Z M649,962 V977 M637,953 H641 M637,960 H641 M637,967 H641"/>
      <circle cx="663" cy="953" r="2"/>
      <path d="M675,957 a6,7 0 1 0 0,12"/>
    </g>
  </svg>

  <div class="feature-label" style="left:138px;top:442px">LED Advertising<br>Display</div>
  <div class="feature-label" style="left:138px;top:630px">Connection<br>to Internet<br>(User Defined)</div>
  <div class="feature-label" style="left:138px;top:834px">800W Solar</div>
  <div class="feature-label" style="left:138px;top:1015px">USB-A &amp; USB-C Cell<br>Phone Charging Ports</div>
  <div class="feature-label" style="left:392px;top:1015px">400ah battery backup<br>with Low Voltage shutoff</div>
  <div class="feature-label" style="left:649px;top:442px">Wireless Cell<br>Phone Charging</div>
  <div class="feature-label" style="left:649px;top:630px">Vandalism<br>Resistant</div>
  <div class="feature-label" style="left:649px;top:822px">Theft<br>Resistant</div>
  <div class="feature-label" style="left:649px;top:1015px">Insulated for<br>40 Deg C</div>

  <footer class="footer">
    <div class="footer-cta">GET A FREE CONSULTATION TODAY</div>
    <div class="footer-phone" style="left:44px">
      <svg viewBox="0 0 20 20"><circle cx="10" cy="10" r="9" fill="var(--paper)"/><path d="M6,5 l3,0 1,3 -2,1 a7,7 0 0 0 3,3 l1,-2 3,1 0,3 a9,9 0 0 1 -9,-9 Z" fill="var(--sky)"/></svg>
      403.555.0182
    </div>
    <div class="footer-phone" style="left:210px">
      <svg viewBox="0 0 20 20"><circle cx="10" cy="10" r="9" fill="var(--paper)"/><path d="M6,5 l3,0 1,3 -2,1 a7,7 0 0 0 3,3 l1,-2 3,1 0,3 a9,9 0 0 1 -9,-9 Z" fill="var(--sky)"/></svg>
      780.555.0147
    </div>
    <div class="footer-divider" style="left:388px"></div>
    <div class="footer-info" style="left:396px">
      <svg viewBox="0 0 12 12"><path d="M6,1 a4,4 0 0 1 4,4 c0,3 -4,6 -4,6 s-4,-3 -4,-6 a4,4 0 0 1 4,-4 Z" fill="var(--paper)"/><circle cx="6" cy="5" r="1.5" fill="var(--sky)"/></svg>
      <span>Birchford,<br>Alberta, Canada</span>
    </div>
    <div class="footer-divider" style="left:514px"></div>
    <div class="footer-contacts">
      <div><svg viewBox="0 0 12 12"><circle cx="6" cy="6" r="6" fill="var(--paper)"/><rect x="3" y="4" width="6" height="4" fill="var(--sky)"/></svg>sales@copperwrenrenewables.com</div>
      <div><svg viewBox="0 0 12 12"><circle cx="6" cy="6" r="6" fill="var(--paper)"/><circle cx="6" cy="6" r="3" fill="none" stroke="var(--sky)" stroke-width="1.2"/></svg>www.copperwrenrenewables.com</div>
    </div>
  </footer>

</main>
</body>
</html>
```